Mailing Brochure

I need a cover for a brochure that we are doing here locally. The only thing I am worried about is the COVER. The size of the brochure is 8.5 x 11 in.
We have a reasonable design for the inserts and back cover. We will mail the packet to accident victims that may need a lawyer. I am including a copy of our current tri-fold brochure that this will replace. The copy from that brochure will be in the inserts. We want something a little similar to that brochure- emphasizing good results and happy people, with maybe a little more legal flavor. I have included photos Pilgrave and the firm's building.
Thanks for your help.

```html
<!DOCTYPE html>
<html lang="en">
<head>
<meta charset="utf-8">
<title>Pilgrave Law Group – Brochure Cover</title>
<link href="https://fonts.googleapis.com/css2?family=Montserrat:wght@300;600;700&family=EB+Garamond:ital,wght@0,400;1,400&display=swap" rel="stylesheet">
<style>
  :root {
    --navy: #0d3a5e;
    --navy-deep: #0a3152;
    --navy-soft: #134670;
    --white: #ffffff;
    --backdrop: #ececec;
    --grey-text: #6b6b6b;
  }
  html, body {
    margin: 0;
    width: 960px;
    height: 1200px;
    overflow: hidden;
    background: var(--backdrop);
  }
  .cover {
    position: absolute;
    left: 70px;
    top: 20px;
    width: 848px;
    height: 1200px;
    transform: scale(0.9667);
    transform-origin: top left;
    overflow: hidden;
    font-family: "Montserrat", sans-serif;
    color: var(--white);
  }
  .cover-art {
    position: absolute;
    inset: 0;
    width: 848px;
    height: 1200px;
  }
  .headline {
    position: absolute;
    left: 396px;
    top: 52px;
    margin: 0;
    font-size: 49px;
    line-height: 65px;
    font-weight: 300;
    letter-spacing: 0.5px;
  }
  .headline strong { font-weight: 700; }
  .brand {
    position: absolute;
    left: 56px;
    top: 830px;
    display: flex;
    align-items: center;
    gap: 14px;
  }
  .brand-square {
    width: 112px;
    height: 112px;
    background: var(--navy);
  }
  .brand-name {
    font-family: "EB Garamond", serif;
    font-weight: 400;
    font-size: 44px;
    line-height: 46px;
    color: var(--navy);
    letter-spacing: 1px;
    text-transform: uppercase;
  }
  .tagline {
    position: absolute;
    left: 52px;
    top: 956px;
    margin: 0;
    font-family: "EB Garamond", serif;
    font-style: italic;
    font-size: 27px;
    color: var(--navy);
  }
  .contact {
    position: absolute;
    right: 34px;
    top: 1070px;
    text-align: center;
    width: 420px;
  }
  .contact-phone {
    font-size: 34px;
    font-weight: 700;
    letter-spacing: 1px;
    margin: 0 0 6px;
  }
  .contact-web, .contact-address {
    font-size: 19px;
    font-weight: 600;
    margin: 0 0 8px;
    letter-spacing: 0.5px;
  }
</style>
</head>
<body>
<main class="cover">
  <svg class="cover-art" viewBox="0 0 848 1200" xmlns="http://www.w3.org/2000/svg">
    <defs>
      <clipPath id="photo-band">
        <path d="M0,458 Q400,300 848,318 L848,862 Q300,722 0,797 Z"/>
      </clipPath>
      <linearGradient id="park-tones" x1="0" y1="0" x2="1" y2="1">
        <stop offset="0" stop-color="#4f7d3a"/>
        <stop offset="0.55" stop-color="#8fae6a"/>
        <stop offset="1" stop-color="#d98aa8"/>
      </linearGradient>
      <linearGradient id="beach-tones" x1="0" y1="0" x2="0" y2="1">
        <stop offset="0" stop-color="#f3efe6"/>
        <stop offset="0.55" stop-color="#d9d2c2"/>
        <stop offset="1" stop-color="#b99a72"/>
      </linearGradient>
    </defs>
    <rect class="bg-navy" width="848" height="1200" fill="var(--navy)"/>
    <path class="bg-wave" d="M0,170 Q420,120 848,190 L848,320 Q420,300 0,340 Z" fill="var(--navy-soft)" opacity="0.35"/>
    <path class="bg-wave" d="M0,340 Q300,230 848,330 L848,470 L0,470 Z" fill="var(--navy-deep)" opacity="0.4"/>

    <g clip-path="url(#photo-band)">
      <rect x="0" y="300" width="343" height="560" fill="url(#park-tones)" role="img" aria-label="Photo: smiling mother and daughter in helmets with their bicycles in a park"/>
      <rect x="347" y="300" width="501" height="570" fill="url(#beach-tones)" role="img" aria-label="Photo: grandfather and two boys running with a kite on a sunny beach"/>
    </g>
    <rect x="343" y="330" width="4" height="480" fill="var(--white)"/>
    <path d="M0,458 Q400,300 848,318" fill="none" stroke="var(--white)" stroke-width="7"/>

    <path class="white-field" d="M0,800 Q300,742 848,884 L848,968 Q400,990 80,1200 L0,1200 Z" fill="var(--white)"/>
    <path class="bottom-wave" d="M80,1200 Q400,990 848,968 L848,1200 Z" fill="var(--navy)"/>
  </svg>

  <h1 class="headline">We’ll help<br>you get <strong>back to</strong><br><strong>what you love</strong></h1>

  <div class="brand">
    <div class="brand-square"></div>
    <div class="brand-name">Pilgrave<br>Law Group</div>
  </div>
  <p class="tagline">Helping Accidents Victim since 1993</p>

  <div class="contact">
    <p class="contact-phone">907 555 0148</p>
    <p class="contact-web">www.pilgravelaw.com</p>
    <p class="contact-address">214 Birch Street • Anchorage, AK 99501</p>
  </div>
</main>
</body>
</html>
```